Climbing Gear Company Stationary Design

We need some new stationary to standardise our business.
We require:

Business Card
A4 Letterhead
With complements slip

Our business is a Distributor and retailer of rock climbing equipment throughout Australia.
We need to the stationary (business card in particular) to reflect this.

Target Market(s)

customers, other retail outlets, overseas manufacturers.

Industry/Entity Type

Business

Requirements
Must have
• company logo
website url- www.ridgetopgearworks.com.au
email - mark@ridgetopgearworks.com
Business Address: Unit 3, 14-16 Marlowe Street, Kestrel Heads, KH, 2371
Phone: 0438 627 194
my Name (on Business card) - Gordon Pellimore
use of Blue colour in our logo

```html
<!DOCTYPE html>
<html lang="en">
<head>
<meta charset="utf-8">
<title>Ridgetop Gearworks – Business Card</title>
<link rel="stylesheet" href="https://fonts.googleapis.com/css2?family=Open+Sans:ital,wght@0,400;0,600;0,800;1,800&display=swap">
<style>
  :root {
    --brand-blue: #213f8b;
    --card-white: #ffffff;
    --ink: #2a2a2a;
    --rule: #c9c9c9;
    --backdrop: #e6e4e1;
  }
  * { margin: 0; padding: 0; box-sizing: border-box; }
  html, body { width: 1200px; height: 440px; overflow: hidden; }
  body {
    background: var(--backdrop);
    font-family: "Open Sans", Arial, sans-serif;
    position: relative;
  }
  .card {
    position: absolute;
    width: 534px;
    height: 306px;
    border-radius: 20px;
    overflow: hidden;
  }
  .card--front { left: 44px; top: 64px; background: var(--card-white); }
  .card--back { left: 612px; top: 66px; background: var(--brand-blue); }

  .brand-name {
    font-weight: 800;
    color: var(--brand-blue);
    text-transform: uppercase;
    letter-spacing: 0.5px;
    white-space: nowrap;
  }
  .tagline {
    color: var(--brand-blue);
    text-transform: uppercase;
    letter-spacing: 3.6px;
    white-space: nowrap;
    font-weight: 400;
  }
  .card--front .brand-name { position: absolute; left: 34px; top: 36px; font-size: 35px; }
  .card--front .tagline { position: absolute; left: 34px; top: 86px; font-size: 16px; }

  .address {
    position: absolute; left: 31px; top: 164px;
    font-size: 13px; line-height: 20px; color: var(--ink);
    font-style: normal;
  }
  .divider {
    position: absolute; left: 245px; top: 157px;
    width: 1px; height: 52px; background: var(--rule);
  }
  .contact {
    position: absolute; left: 288px; top: 155px;
    font-size: 13px; line-height: 19px; color: var(--ink);
    list-style: none;
  }
  .contact li { display: flex; align-items: center; gap: 6px; }
  .contact svg { width: 10px; height: 10px; fill: var(--ink); }
  .contact .web { margin-top: 3px; }

  .wave { position: absolute; left: 0; bottom: 0; width: 534px; height: 100px; }
  .holder-name {
    position: absolute; left: 31px; top: 266px;
    font-size: 19px; font-weight: 800; font-style: italic;
    color: var(--card-white); text-transform: uppercase; letter-spacing: 0.2px;
  }

  .band {
    position: absolute; left: 0; top: 131px; width: 100%; height: 86px;
    background: var(--card-white);
    display: flex; flex-direction: column; align-items: center; justify-content: center;
  }
  .card--back .brand-name { font-size: 31px; line-height: 36px; }
  .card--back .tagline { font-size: 14px; letter-spacing: 3.2px; margin-top: 2px; }
</style>
</head>
<body>
  <section class="card card--front" aria-label="Business card front">
    <div class="brand-name">Ridgetop Gearworks</div>
    <div class="tagline">The Rope • The Crag • The Summit</div>

    <address class="address">
      Unit 3, 14-16 Marlowe Street<br>
      Kestrel Heads, KH, 2371
    </address>
    <div class="divider"></div>
    <ul class="contact">
      <li>
        <svg viewBox="0 0 10 10" aria-hidden="true"><path d="M2 0.5 L3.6 2.6 L2.7 3.6 C3.3 5 4.6 6.5 6.2 7.3 L7.2 6.4 L9.4 8 L8.4 9.5 C4.5 9.2 0.8 5.4 0.6 1.6 Z"/></svg>
        0438 627 194
      </li>
      <li>
        <svg viewBox="0 0 10 10" aria-hidden="true"><path d="M0.5 2 H9.5 V8.5 H0.5 Z M1.5 3 V7.5 H8.5 V3 L5 5.6 Z" fill-rule="evenodd"/></svg>
        mark@ridgetopgearworks.com
      </li>
      <li class="web">www.RIDGETOPGEARWORKS.COM.au</li>
    </ul>

    <svg class="wave" viewBox="0 0 534 100" preserveAspectRatio="none" aria-hidden="true">
      <path d="M0 28 C80 10 160 2 240 10 C320 18 400 38 470 28 C500 24 520 18 534 14" fill="none" stroke="var(--brand-blue)" stroke-width="3"/>
      <path d="M0 34 C80 16 160 8 240 16 C320 24 400 44 470 34 C500 30 520 24 534 20 L534 100 L0 100 Z" fill="var(--brand-blue)"/>
      <path d="M110 22 C190 18 270 26 340 40 C390 50 440 48 500 34" fill="none" stroke="var(--card-white)" stroke-width="3"/>
    </svg>
    <div class="holder-name">Gordon Pellimore</div>
  </section>

  <section class="card card--back" aria-label="Business card back">
    <div class="band">
      <div class="brand-name">Ridgetop Gearworks</div>
      <div class="tagline">The Rope • The Crag • The Summit</div>
    </div>
  </section>
</body>
</html>
```